Delivery Performance Dashboard for Web Portal

We need you to design a dashboard for our web portal. We deliver sand and stone to construction jobsites. The attached screenshot is from our current web portal dashboard . It shows how much material has been delivered from an order.

Gravel Line will deliver multiple loads during the day and the dispatcher uses the dashboard to monitor if they need to add more trucks or less trucks to fulfill the order. An example would be, I need to ship 1,000 tons of sand to a jobsite and I plan to use 10 trucks during the day and that it will take 10 hours of hauling to complete the job. After 5 hours of hauling (50% the day is over), I should have delivered 500 tons of sand (50% of the order). But maybe there is a lot of traffic, and I only have delivered 300 tons. The dashboard will show that I am behind schedule and I might need to add 2 more trucks to the job.

Industry/Entity Type

Construction

Font styles to use
Sans Serif

Requirements
Must have
• We need a progress bar showing how much material has been delivered, how much material was requested to be delivered total and how much material should have been delivered at the current time. The goal is to show the user if the deliveries are ahead or behind the expected pace and why.
Nice to have
• The icons for plant, driving and jobsite show if the actual times have exceeded or beaten the planned times. Maybe you have other ideas to show the user if the trucks are sitting longer on the jobsite, at the plant to get loaded or driving to and from the jobsite.

```html
<!DOCTYPE html>
<html lang="en">
<head>
<meta charset="utf-8">
<title>Gravel Line – Delivery Performance Dashboard</title>
<link href="https://fonts.googleapis.com/css2?family=Montserrat:wght@400;500;600;700;800&display=swap" rel="stylesheet">
<style>
:root{
  --stage:#8f8f93;
  --navy:#10265a;
  --content:#eef4fb;
  --white:#ffffff;
  --ink:#2b2b2b;
  --muted:#555b66;
  --line:#d9dee6;
  --head:#3d3b3b;
  --green:#1f9b3a;
  --green-text:#2aa13f;
  --red:#e0261c;
  --orange:#ef8a1b;
  --track:#e4d8d5;
  --icon-grey:#8a8a8a;
  --popup-blue:#1a6fb6;
  --bar-track:#ffffff;
}
*{box-sizing:border-box;margin:0;padding:0}
html,body{width:1200px;height:2431px;overflow:hidden;background:var(--stage)}
body{font-family:"Montserrat",sans-serif;color:var(--ink)}
.board{position:absolute;left:0;top:0;width:1272px;height:2576px;transform:scale(0.943396);transform-origin:0 0}
.screen{position:absolute;left:83px;width:1107px;height:1178px;background:var(--content);overflow:visible}
.screen-a{top:84px}.screen-b{top:1314px}
.topbar{position:absolute;left:0;top:0;width:1107px;height:50px;background:var(--navy)}
.sidebar{position:absolute;left:0;top:50px;width:116px;height:1128px;background:var(--navy)}
.abs{position:absolute}
.menu-toggle{left:22px;top:18px}
.brand{left:128px;top:10px;font-size:23px;font-weight:800;color:var(--white);letter-spacing:.3px}
.search{left:677px;top:10px;width:206px;height:32px;border-radius:16px;background:var(--white);font-size:12px;color:#333;padding:9px 0 0 16px}
.search-btn{position:absolute;right:4px;top:3px;width:26px;height:26px;border-radius:50%;background:var(--green)}
.search-btn svg{position:absolute;left:7px;top:7px}
.welcome{right:99px;top:7px;text-align:right;color:var(--white)}
.welcome small{display:block;font-size:11px}
.welcome strong{display:block;font-size:15px;font-weight:700;margin-top:1px}
.avatar{left:1018px;top:2px;width:46px;height:46px;border-radius:50%;background:linear-gradient(160deg,#c8ccd2,#6d7178);border:2px solid #dfe3ea}
.nav{position:absolute;left:10px;top:22px;list-style:none}
.nav li{display:flex;align-items:center;height:31.4px;font-size:10.5px;color:var(--white)}
.nav svg{margin-right:9px}
.nav .caret{margin-left:6px;width:0;height:0;border-left:3px solid transparent;border-right:3px solid transparent;border-top:4px solid var(--white)}
.stat{top:72px;width:306px;height:133px;color:var(--white)}
.stat-orders{left:147px;background:linear-gradient(90deg,#5ec8c1,#91e0da)}
.stat-moves{left:461px;background:linear-gradient(90deg,#4e8ed2,#8fc6ea)}
.stat-success{left:774px;background:linear-gradient(90deg,#dcae42,#f1d68d)}
.stat svg{position:absolute;left:46px;top:34px}
.stat-label{position:absolute;left:162px;top:34px;font-size:16.5px;font-weight:500}
.stat-value{position:absolute;left:162px;top:64px;font-size:28px;font-weight:800;letter-spacing:.5px}
.panel{background:var(--white);border:1px solid var(--line)}
.panel-stop{left:147px;top:217px;width:620px;height:257px}
.panel-site{left:774px;top:217px;width:306px;height:257px}
.panel-title{position:absolute;top:20px;font-size:25px;font-weight:700;color:#222}
.gauge{position:absolute;top:0;left:0}
.gauge-text{position:absolute;width:150px;text-align:center;top:125px}
.gauge-text b{display:block;font-size:39px;font-weight:700;line-height:1;color:#1e1e1e;letter-spacing:-.5px}
.gauge-text span{display:block;font-size:10px;margin-top:6px;color:#222}
.panel-orders{left:147px;top:487px;width:933px;height:257px}
.panel-tons{left:147px;top:758px;width:933px;height:258px}
table{position:absolute;left:13px;top:14px;width:907px;border-collapse:collapse;font-size:11px;color:var(--muted)}
th{background:var(--head);color:var(--white);font-weight:600;font-size:11.5px;height:37px;text-align:left;padding-left:20px;position:relative}
td{height:47px;border:1px solid var(--line);padding-left:20px;background:var(--white)}
th .sort{position:absolute;right:20px;top:13px}
.pager{position:absolute;top:212px;display:flex;gap:9px;right:13px}
.pager span{width:27px;height:25px;border:1px solid #9aa0a8;background:var(--white);font-size:11px;display:flex;align-items:center;justify-content:center;color:#333}
.pager .on{background:var(--green);border-color:var(--green);color:var(--white);font-weight:700}
.panel-tons .pager{top:213px}
.prog{position:relative;height:47px}
.bar{position:absolute;left:0;top:10px;width:272px;height:9px;border:1px solid #d3d7dd;border-radius:5px;background:var(--bar-track);overflow:hidden}
.bar i{display:block;height:100%;background:linear-gradient(90deg,#1a7dd4,#3fc6e8)}
.prog .amt,.prog .window{position:absolute;top:28px;font-size:9px;color:#444}
.prog .window{right:10px}
.wait{display:flex;align-items:center;gap:6px;padding-left:26px}
.remain{color:var(--green-text);text-align:center;padding-left:0}
.delta{color:var(--red);padding-left:60px}
.footer{position:absolute;left:0;top:1130px;width:1107px;padding-left:20px;text-align:center;font-size:10.5px;color:#333}
.popup{left:512px;top:854px;width:245px;height:319px;background:var(--white);box-shadow:0 4px 18px rgba(0,0,0,.22)}
.popup h3{position:absolute;left:25px;top:14px;font-size:17.5px;font-weight:500;color:#1e1e1e}
.pop-row{position:absolute;left:4px;width:237px;border-top:1px solid #e4e6ea;font-size:10.5px;color:#222}
.pop-row svg{position:absolute;left:16px}
.pop-row .desc{position:absolute;left:60px;line-height:1.45}
.pop-row .actual{position:absolute;left:170px}
</style>
</head>
<body>
<svg width="0" height="0" style="position:absolute">
  <defs>
    <symbol id="i-factory" viewBox="0 0 20 18"><path d="M1 17V2h3v8l5-4v4l5-4v4l5-4v11z" fill="currentColor"/></symbol>
    <symbol id="i-truck" viewBox="0 0 22 16"><path d="M1 2h12v10H1zM14 5h4l3 4v3h-7z" fill="currentColor"/><circle cx="5" cy="13.5" r="2.2" fill="currentColor" stroke="#fff" stroke-width="1"/><circle cx="17" cy="13.5" r="2.2" fill="currentColor" stroke="#fff" stroke-width="1"/></symbol>
    <symbol id="i-pin" viewBox="0 0 14 20"><path d="M7 1a6 6 0 0 1 6 6c0 4.5-6 12-6 12S1 11.5 1 7a6 6 0 0 1 6-6z" fill="none" stroke="currentColor" stroke-width="2"/><circle cx="7" cy="7" r="2.2" fill="currentColor"/></symbol>
    <symbol id="i-pin-solid" viewBox="0 0 14 20"><path d="M7 1a6 6 0 0 1 6 6c0 4.5-6 12-6 12S1 11.5 1 7a6 6 0 0 1 6-6z" fill="currentColor"/><circle cx="7" cy="7" r="2.4" fill="#fff"/></symbol>
    <symbol id="i-up" viewBox="0 0 10 8"><path d="M5 0l5 8H0z" fill="#e0261c"/></symbol>
    <symbol id="i-down" viewBox="0 0 10 8"><path d="M0 0h10L5 8z" fill="#1f9b3a"/></symbol>
    <symbol id="i-dash" viewBox="0 0 12 4"><rect width="12" height="3" rx="1" fill="#8a8a8a"/></symbol>
    <symbol id="i-sort" viewBox="0 0 8 12"><path d="M4 0l4 5H0zM0 7h8l-4 5z" fill="#fff"/></symbol>
    <symbol id="i-truck-outline" viewBox="0 0 84 64"><g fill="none" stroke="#fff" stroke-width="4" stroke-linejoin="round"><path d="M3 6h48v42H3zM51 20h16l12 14v14H51z"/><path d="M57 24h9l7 9H57z"/><circle cx="16" cy="50" r="7" fill="currentColor"/><circle cx="66" cy="50" r="7" fill="currentColor"/></g></symbol>
    <symbol id="i-cargo-truck" viewBox="0 0 100 64"><g fill="none" stroke="#fff" stroke-width="4" stroke-linejoin="round"><path d="M10 4h18v18H10zM28 4h18v18H28zM10 22h18v18H10zM28 22h18v18H28z"/><path d="M3 40h60V18h14l14 16v14H3z"/><path d="M66 22h9l8 10H66z"/><path d="M54 8h12v10"/><circle cx="18" cy="50" r="8"/><circle cx="80" cy="50" r="8"/></g></symbol>
    <symbol id="i-clock-truck" viewBox="0 0 100 80"><g fill="none" stroke="#fff" stroke-width="4" stroke-linejoin="round"><circle cx="24" cy="24" r="20"/><circle cx="24" cy="24" r="13"/><path d="M24 15v10h8"/><path d="M40 20h22v44H12V44M62 34h14l14 16v14H62z"/><path d="M66 38h8l8 10H66z"/><circle cx="26" cy="68" r="8"/><circle cx="78" cy="68" r="8"/></g></symbol>
  </defs>
</svg>

<div class="board">

<!-- ===== Dashboard ===== -->
<section class="screen screen-a">
  <header class="topbar">
    <svg class="abs menu-toggle" width="18" height="14" viewBox="0 0 18 14"><rect width="18" height="2.6" fill="#fff"/><rect y="5.7" width="18" height="2.6" fill="#fff"/><rect y="11.4" width="18" height="2.6" fill="#fff"/></svg>
    <div class="abs brand">GRAVEL LINE</div>
    <div class="abs search">Search<span class="search-btn"><svg width="12" height="12" viewBox="0 0 12 12"><circle cx="5" cy="5" r="3.4" fill="none" stroke="#fff" stroke-width="1.6"/><path d="M7.5 7.5l3 3" stroke="#fff" stroke-width="1.6"/></svg></span></div>
    <div class="abs welcome"><small>Welcome</small><strong>Sam Rivers</strong></div>
    <div class="abs avatar" role="img" aria-label="User profile photo"></div>
  </header>
  <nav class="sidebar">
    <ul class="nav">
      <li><svg width="14" height="14" viewBox="0 0 14 14" fill="none" stroke="#fff" stroke-width="1"><path d="M1 7l6-5 6 5M3 6v7h8V6"/></svg>Home</li>
      <li><svg width="14" height="14" viewBox="0 0 14 14" fill="none" stroke="#fff" stroke-width="1"><rect x="1" y="2" width="12" height="3"/><rect x="1" y="6" width="12" height="3"/><rect x="1" y="10" width="12" height="3"/></svg>Timesheets<span class="caret"></span></li>
      <li><svg width="14" height="14" viewBox="0 0 14 14" fill="none" stroke="#fff" stroke-width="1"><circle cx="7" cy="7" r="6"/><path d="M7 6v5M7 3.5v1"/></svg>Samples<span class="caret"></span></li>
      <li><svg width="14" height="14" viewBox="0 0 14 14" fill="none" stroke="#fff" stroke-width="1"><circle cx="7" cy="7" r="2.2"/><circle cx="7" cy="7" r="5.5" stroke-dasharray="2 1.5"/></svg>Reports</li>
      <li><svg width="14" height="14" viewBox="0 0 14 14" fill="none" stroke="#fff" stroke-width="1"><rect x="1.5" y="1" width="11" height="12"/><path d="M3.5 3.5h7M3.5 6h2M6 6h2M8.5 6h2M3.5 8.5h2M6 8.5h2M8.5 8.5h2M3.5 11h2M6 11h2M8.5 11h2"/></svg>Estimates</li>
      <li><svg width="14" height="14" viewBox="0 0 14 14" fill="none" stroke="#fff" stroke-width="1"><path d="M3 1.5l2 3-1.2 1.4a7 7 0 0 0 4.3 4.3L9.5 9l3 2-1.5 2C6 13 1 8 1 3z"/></svg>Contact</li>
    </ul>
  </nav>

  <div class="abs stat stat-orders"><svg width="84" height="64"><use href="#i-truck-outline" color="#7dd6cf"/></svg><div class="stat-label">Total orders</div><div class="stat-value">34</div></div>
  <div class="abs stat stat-moves"><svg width="100" height="64"><use href="#i-cargo-truck"/></svg><div class="stat-label">Good Moves</div><div class="stat-value">7400</div></div>
  <div class="abs stat stat-success"><svg width="90" height="72" viewBox="0 0 100 80" style="top:30px;left:22px"><use href="#i-clock-truck"/></svg><div class="stat-label" style="left:142px">Delivery Success</div><div class="stat-value" style="left:142px">85%</div></div>

  <div class="abs panel panel-stop">
    <div class="panel-title" style="left:59px">Truck Stop</div>
    <svg class="gauge" width="620" height="257" viewBox="147 217 620 257">
      <g fill="none" stroke="var(--track)" stroke-width="4"><circle cx="283" cy="371" r="72"/><circle cx="463" cy="371" r="72"/><circle cx="643" cy="371" r="72"/></g>
      <path d="M211 371A72 72 0 0 1 283 299" fill="none" stroke="var(--green)" stroke-width="5"/>
      <path d="M405 327A72 72 0 0 1 463 299" fill="none" stroke="var(--orange)" stroke-width="5"/>
      <path d="M643 299A72 72 0 0 0 608 434" fill="none" stroke="var(--navy)" stroke-width="5"/>
    </svg>
    <div class="gauge-text" style="left:61px"><b>75%</b><span>Current Capacity</span></div>
    <div class="gauge-text" style="left:241px"><b>9,358</b><span>Weekly Avg Capacity</span></div>
    <div class="gauge-text" style="left:421px"><b>12</b><span>Yearly Avg capacity</span></div>
  </div>

  <div class="abs panel panel-site">
    <div class="panel-title" style="left:48px">Site Activity</div>
    <svg class="abs" style="left:0;top:0" width="306" height="257" viewBox="774 217 306 257" font-family="Montserrat, sans-serif">
      <text x="818" y="302" font-size="3.5" fill="#777">Line Chart</text>
      <text x="818" y="308" font-size="2.6" fill="#999">Site loads by month this year</text>
      <g stroke="#e8eaee" stroke-width=".5">
        <path d="M812 314H1038M812 323H1038M812 332H1038M812 341H1038M812 350H1038M812 359H1038M812 368H1038M812 377H1038M812 386H1038M812 395H1038M812 404H1038M812 413H1038"/>
        <path d="M818 314V416M836 314V416M854 314V416M873 314V416M891 314V416M909 314V416M927 314V416M945 314V416M963 314V416M981 314V416M1000 314V416M1018 314V416M1036 314V416"/>
      </g>
      <g font-size="2.6" fill="#999" text-anchor="end">
        <text x="810" y="315">100%</text><text x="810" y="324">90%</text><text x="810" y="333">80%</text><text x="810" y="342">70%</text><text x="810" y="351">60%</text><text x="810" y="360">50%</text><text x="810" y="369">40%</text><text x="810" y="378">30%</text><text x="810" y="387">20%</text><text x="810" y="396">10%</text>
      </g>
      <polyline points="818,413 836,386 854,403 873,383 891,334 909,353 927,344 945,373 963,375 981,376 1000,363 1018,334 1036,354" fill="none" stroke="#222" stroke-width="1"/>
      <polyline points="818,373 836,354 854,384 873,403 891,386 909,374 927,326 945,356 963,391 981,384 1000,354 1018,354 1036,374" fill="none" stroke="#3dc23d" stroke-width="1"/>
      <g font-size="2.6" fill="#999" text-anchor="middle">
        <text x="818" y="424">Jan</text><text x="836" y="424">Feb</text><text x="854" y="424">Mar</text><text x="873" y="424">Apr</text><text x="891" y="424">May</text><text x="909" y="424">Jun</text><text x="927" y="424">Jul</text><text x="945" y="424">Aug</text><text x="963" y="424">Sep</text><text x="981" y="424">Oct</text><text x="1000" y="424">Nov</text><text x="1018" y="424">Dec</text>
      </g>
      <circle cx="828" cy="439" r="1" fill="#222"/><text x="831" y="440" font-size="2.6" fill="#999">Loads</text>
      <circle cx="862" cy="439" r="1" fill="#3dc23d"/><text x="865" y="440" font-size="2.6" fill="#999">Target</text>
    </svg>
  </div>

  <div class="abs panel panel-orders">
    <table>
      <tr><th style="width:152px">ORDER<svg class="sort" width="8" height="12"><use href="#i-sort"/></svg></th><th style="width:153px">ORIGIN<svg class="sort" width="8" height="12"><use href="#i-sort"/></svg></th><th style="width:231px">DESTINATION<svg class="sort" width="8" height="12"><use href="#i-sort"/></svg></th><th style="width:232px;padding-left:28px">CUSTOMER<svg class="sort" width="8" height="12"><use href="#i-sort"/></svg></th><th>STATUS<svg class="sort" width="8" height="12"><use href="#i-sort"/></svg></th></tr>
      <tr><td>17746</td><td>Sed ut perspiciatis</td><td>BJV - 156 ste natus error sit</td><td style="padding-left:28px">Construction - North Division</td><td>Accepted</td></tr>
      <tr><td>12468</td><td>Quis autem vel eum</td><td>DJV - 126 Excepteur sint occaeca</td><td style="padding-left:28px">Construction - North Division</td><td>Accepted</td></tr>
      <tr><td>17746</td><td>Sed ut perspiciatis</td><td>BJV - 156 ste natus error sit</td><td style="padding-left:28px">Construction - North Division</td><td>Accepted</td></tr>
    </table>
    <div class="pager"><span>«</span><span class="on">1</span><span>»</span></div>
  </div>

  <div class="abs panel panel-tons">
    <table>
      <tr><th style="width:305px">TONS</th><th style="width:231px">WAIT TIMES</th><th style="width:232px;text-align:center;padding-left:0"><svg width="10" height="10" viewBox="0 0 10 10" style="vertical-align:-1px;margin-right:5px"><circle cx="5" cy="5" r="4" fill="none" stroke="#fff" stroke-width="1.4"/><path d="M5 3v2.4h1.8" stroke="#fff" stroke-width="1.2" fill="none"/></svg>REMAINING</th><th>+/- <svg width="13" height="10" style="vertical-align:-1px;margin-left:4px"><use href="#i-truck" color="#fff"/></svg></th></tr>
      <tr><td><div class="prog"><div class="bar"><i style="width:66%"></i></div><span class="amt">722.76 / 1500</span><span class="window">7:30am : 5:00pm</span></div></td>
        <td><div class="wait"><svg width="20" height="18" style="color:var(--icon-grey)"><use href="#i-factory"/></svg><svg width="10" height="8" style="margin:0 22px 0 8px"><use href="#i-up"/></svg><svg width="22" height="16" style="color:var(--icon-grey)"><use href="#i-truck"/></svg><svg width="10" height="8" style="margin:0 12px 0 4px"><use href="#i-up"/></svg><svg width="12" height="18" style="color:var(--icon-grey)"><use href="#i-pin"/></svg><svg width="10" height="8" style="margin-left:4px"><use href="#i-down"/></svg></div></td>
        <td class="remain">+ 1 : 25 hrs</td><td class="delta">-31</td></tr>
      <tr><td><div class="prog"><div class="bar"><i style="width:99%"></i></div><span class="amt">722.76 / 1500</span><span class="window">7:30am : 5:00pm</span></div></td>
        <td><div class="wait"><svg width="20" height="18" style="color:var(--icon-grey)"><use href="#i-factory"/></svg><svg width="10" height="8" style="margin:0 22px 0 8px"><use href="#i-up"/></svg><svg width="22" height="16" style="color:var(--icon-grey)"><use href="#i-truck"/></svg><svg width="10" height="8" style="margin:0 12px 0 4px"><use href="#i-up"/></svg><svg width="12" height="18" style="color:var(--icon-grey)"><use href="#i-pin"/></svg><svg width="10" height="8" style="margin-left:4px"><use href="#i-down"/></svg></div></td>
        <td class="remain">+ 1 : 25 hrs</td><td class="delta">-31</td></tr>
      <tr><td><div class="prog"><div class="bar"><i style="width:0"></i></div><span class="amt">0.00 / 100</span><span class="window">8:00pm : 4:00am</span></div></td>
        <td><div class="wait"><svg width="20" height="18" style="color:var(--icon-grey)"><use href="#i-factory"/></svg><svg width="14" height="4" style="margin:0 18px 0 8px"><use href="#i-dash"/></svg><svg width="22" height="16" style="color:var(--icon-grey)"><use href="#i-truck"/></svg><svg width="14" height="4" style="margin:0 12px 0 4px"><use href="#i-dash"/></svg><svg width="12" height="18" style="color:var(--icon-grey)"><use href="#i-pin"/></svg><svg width="14" height="4" style="margin-left:4px"><use href="#i-dash"/></svg></div></td>
        <td class="remain">+ 1 : 25 hrs</td><td class="delta">-31</td></tr>
    </table>
    <div class="pager"><span>«</span><span class="on">1</span><span>»</span></div>
  </div>

  <footer class="footer">© 2020 Gravel Line All rights Reserved &nbsp;|&nbsp; Privacy &nbsp;|&nbsp; Terms and Use &nbsp;|&nbsp; End user agreement &nbsp;|&nbsp; Cookie references</footer>
</section>

<!-- ===== Dashboard with order detail ===== -->
<section class="screen screen-b">
  <header class="topbar">
    <svg class="abs menu-toggle" width="18" height="14" viewBox="0 0 18 14"><rect width="18" height="2.6" fill="#fff"/><rect y="5.7" width="18" height="2.6" fill="#fff"/><rect y="11.4" width="18" height="2.6" fill="#fff"/></svg>
    <div class="abs brand">GRAVEL LINE</div>
    <div class="abs search">Search<span class="search-btn"><svg width="12" height="12" viewBox="0 0 12 12"><circle cx="5" cy="5" r="3.4" fill="none" stroke="#fff" stroke-width="1.6"/><path d="M7.5 7.5l3 3" stroke="#fff" stroke-width="1.6"/></svg></span></div>
    <div class="abs welcome"><small>Welcome</small><strong>Sam Rivers</strong></div>
    <div class="abs avatar" role="img" aria-label="User profile photo"></div>
  </header>
  <nav class="sidebar">
    <ul class="nav">
      <li><svg width="14" height="14" viewBox="0 0 14 14" fill="none" stroke="#fff" stroke-width="1"><path d="M1 7l6-5 6 5M3 6v7h8V6"/></svg>Home</li>
      <li><svg width="14" height="14" viewBox="0 0 14 14" fill="none" stroke="#fff" stroke-width="1"><rect x="1" y="2" width="12" height="3"/><rect x="1" y="6" width="12" height="3"/><rect x="1" y="10" width="12" height="3"/></svg>Timesheets<span class="caret"></span></li>
      <li><svg width="14" height="14" viewBox="0 0 14 14" fill="none" stroke="#fff" stroke-width="1"><circle cx="7" cy="7" r="6"/><path d="M7 6v5M7 3.5v1"/></svg>Samples<span class="caret"></span></li>
      <li><svg width="14" height="14" viewBox="0 0 14 14" fill="none" stroke="#fff" stroke-width="1"><circle cx="7" cy="7" r="2.2"/><circle cx="7" cy="7" r="5.5" stroke-dasharray="2 1.5"/></svg>Reports</li>
      <li><svg width="14" height="14" viewBox="0 0 14 14" fill="none" stroke="#fff" stroke-width="1"><rect x="1.5" y="1" width="11" height="12"/><path d="M3.5 3.5h7M3.5 6h2M6 6h2M8.5 6h2M3.5 8.5h2M6 8.5h2M8.5 8.5h2M3.5 11h2M6 11h2M8.5 11h2"/></svg>Estimates</li>
      <li><svg width="14" height="14" viewBox="0 0 14 14" fill="none" stroke="#fff" stroke-width="1"><path d="M3 1.5l2 3-1.2 1.4a7 7 0 0 0 4.3 4.3L9.5 9l3 2-1.5 2C6 13 1 8 1 3z"/></svg>Contact</li>
    </ul>
  </nav>

  <div class="abs stat stat-orders"><svg width="84" height="64"><use href="#i-truck-outline" color="#7dd6cf"/></svg><div class="stat-label">Total orders</div><div class="stat-value">34</div></div>
  <div class="abs stat stat-moves"><svg width="100" height="64"><use href="#i-cargo-truck"/></svg><div class="stat-label">Good Moves</div><div class="stat-value">7400</div></div>
  <div class="abs stat stat-success"><svg width="90" height="72" viewBox="0 0 100 80" style="top:30px;left:22px"><use href="#i-clock-truck"/></svg><div class="stat-label" style="left:142px">Delivery Success</div><div class="stat-value" style="left:142px">85%</div></div>

  <div class="abs panel panel-stop">
    <div class="panel-title" style="left:59px">Truck Stop</div>
    <svg class="gauge" width="620" height="257" viewBox="147 217 620 257">
      <g fill="none" stroke="var(--track)" stroke-width="4"><circle cx="283" cy="371" r="72"/><circle cx="463" cy="371" r="72"/><circle cx="643" cy="371" r="72"/></g>
      <path d="M211 371A72 72 0 0 1 283 299" fill="none" stroke="var(--green)" stroke-width="5"/>
      <path d="M405 327A72 72 0 0 1 463 299" fill="none" stroke="var(--orange)" stroke-width="5"/>
      <path d="M643 299A72 72 0 0 0 608 434" fill="none" stroke="var(--navy)" stroke-width="5"/>
    </svg>
    <div class="gauge-text" style="left:61px"><b>75%</b><span>Current Capacity</span></div>
    <div class="gauge-text" style="left:241px"><b>9,358</b><span>Weekly Avg Capacity</span></div>
    <div class="gauge-text" style="left:421px"><b>12</b><span>Yearly Avg capacity</span></div>
  </div>

  <div class="abs panel panel-site">
    <div class="panel-title" style="left:48px">Site Activity</div>
    <svg class="abs" style="left:0;top:0" width="306" height="257" viewBox="774 217 306 257" font-family="Montserrat, sans-serif">
      <text x="818" y="302" font-size="3.5" fill="#777">Line Chart</text>
      <text x="818" y="308" font-size="2.6" fill="#999">Site loads by month this year</text>
      <g stroke="#e8eaee" stroke-width=".5">
        <path d="M812 314H1038M812 323H1038M812 332H1038M812 341H1038M812 350H1038M812 359H1038M812 368H1038M812 377H1038M812 386H1038M812 395H1038M812 404H1038M812 413H1038"/>
        <path d="M818 314V416M836 314V416M854 314V416M873 314V416M891 314V416M909 314V416M927 314V416M945 314V416M963 314V416M981 314V416M1000 314V416M1018 314V416M1036 314V416"/>
      </g>
      <g font-size="2.6" fill="#999" text-anchor="end">
        <text x="810" y="315">100%</text><text x="810" y="324">90%</text><text x="810" y="333">80%</text><text x="810" y="342">70%</text><text x="810" y="351">60%</text><text x="810" y="360">50%</text><text x="810" y="369">40%</text><text x="810" y="378">30%</text><text x="810" y="387">20%</text><text x="810" y="396">10%</text>
      </g>
      <polyline points="818,413 836,386 854,403 873,383 891,334 909,353 927,344 945,373 963,375 981,376 1000,363 1018,334 1036,354" fill="none" stroke="#222" stroke-width="1"/>
      <polyline points="818,373 836,354 854,384 873,403 891,386 909,374 927,326 945,356 963,391 981,384 1000,354 1018,354 1036,374" fill="none" stroke="#3dc23d" stroke-width="1"/>
      <g font-size="2.6" fill="#999" text-anchor="middle">
        <text x="818" y="424">Jan</text><text x="836" y="424">Feb</text><text x="854" y="424">Mar</text><text x="873" y="424">Apr</text><text x="891" y="424">May</text><text x="909" y="424">Jun</text><text x="927" y="424">Jul</text><text x="945" y="424">Aug</text><text x="963" y="424">Sep</text><text x="981" y="424">Oct</text><text x="1000" y="424">Nov</text><text x="1018" y="424">Dec</text>
      </g>
      <circle cx="828" cy="439" r="1" fill="#222"/><text x="831" y="440" font-size="2.6" fill="#999">Loads</text>
      <circle cx="862" cy="439" r="1" fill="#3dc23d"/><text x="865" y="440" font-size="2.6" fill="#999">Target</text>
    </svg>
  </div>

  <div class="abs panel panel-orders">
    <table>
      <tr><th style="width:152px">ORDER<svg class="sort" width="8" height="12"><use href="#i-sort"/></svg></th><th style="width:153px">ORIGIN<svg class="sort" width="8" height="12"><use href="#i-sort"/></svg></th><th style="width:231px">DESTINATION<svg class="sort" width="8" height="12"><use href="#i-sort"/></svg></th><th style="width:232px;padding-left:28px">CUSTOMER<svg class="sort" width="8" height="12"><use href="#i-sort"/></svg></th><th>STATUS<svg class="sort" width="8" height="12"><use href="#i-sort"/></svg></th></tr>
      <tr><td>17746</td><td>Sed ut perspiciatis</td><td>BJV - 156 ste natus error sit</td><td style="padding-left:28px">Construction - North Division</td><td>Accepted</td></tr>
      <tr><td>12468</td><td>Quis autem vel eum</td><td>DJV - 126 Excepteur sint occaeca</td><td style="padding-left:28px">Construction - North Division</td><td>Accepted</td></tr>
      <tr><td>17746</td><td>Sed ut perspiciatis</td><td>BJV - 156 ste natus error sit</td><td style="padding-left:28px">Construction - North Division</td><td>Accepted</td></tr>
    </table>
    <div class="pager"><span>«</span><span class="on">1</span><span>»</span></div>
  </div>

  <div class="abs panel panel-tons">
    <table>
      <tr><th style="width:305px">TONS</th><th style="width:231px">WAIT TIMES</th><th style="width:232px;text-align:center;padding-left:0"><svg width="10" height="10" viewBox="0 0 10 10" style="vertical-align:-1px;margin-right:5px"><circle cx="5" cy="5" r="4" fill="none" stroke="#fff" stroke-width="1.4"/><path d="M5 3v2.4h1.8" stroke="#fff" stroke-width="1.2" fill="none"/></svg>REMAINING</th><th>+/- <svg width="13" height="10" style="vertical-align:-1px;margin-left:4px"><use href="#i-truck" color="#fff"/></svg></th></tr>
      <tr><td><div class="prog"><div class="bar"><i style="width:66%"></i></div><span class="amt">722.76 / 1500</span><span class="window">7:30am : 5:00pm</span></div></td>
        <td><div class="wait"><svg width="20" height="18" style="color:var(--icon-grey)"><use href="#i-factory"/></svg><svg width="10" height="8" style="margin:0 22px 0 8px"><use href="#i-up"/></svg><svg width="22" height="16" style="color:var(--icon-grey)"><use href="#i-truck"/></svg><svg width="10" height="8" style="margin:0 12px 0 4px"><use href="#i-up"/></svg><svg width="12" height="18" style="color:var(--icon-grey)"><use href="#i-pin"/></svg><svg width="10" height="8" style="margin-left:4px"><use href="#i-down"/></svg></div></td>
        <td class="remain">+ 1 : 25 hrs</td><td class="delta">-31</td></tr>
      <tr><td><div class="prog"><div class="bar"><i style="width:99%"></i></div><span class="amt">722.76 / 1500</span><span class="window">7:30am : 5:00pm</span></div></td>
        <td></td><td class="remain">+ 1 : 25 hrs</td><td class="delta">-31</td></tr>
      <tr><td><div class="prog"><div class="bar"><i style="width:0"></i></div><span class="amt">0.00 / 100</span><span class="window">8:00pm : 4:00am</span></div></td>
        <td></td><td class="remain">+ 1 : 25 hrs</td><td class="delta">-31</td></tr>
    </table>
    <div class="pager"><span>«</span><span class="on">1</span><span>»</span></div>
  </div>

  <footer class="footer">© 2020 Gravel Line All rights Reserved &nbsp;|&nbsp; Privacy &nbsp;|&nbsp; Terms and Use &nbsp;|&nbsp; End user agreement &nbsp;|&nbsp; Cookie references</footer>

  <div class="abs popup">
    <h3>Order : 17746</h3>
    <div class="pop-row" style="top:45px;height:53px">
      <svg width="26" height="20" viewBox="0 0 26 20" style="top:16px"><g fill="none" stroke="var(--popup-blue)" stroke-width="2"><path d="M2 6h21M18 1l5 5-5 5"/><path d="M24 14H3M8 9l-5 5 5 5"/></g></svg>
      <span class="desc" style="top:18px">Avg Cycle Time : 2 hr 27min</span>
    </div>
    <div class="pop-row" style="top:98px;height:52px">
      <svg width="26" height="22" style="top:14px;color:var(--popup-blue)"><use href="#i-factory"/></svg>
      <span class="desc" style="top:10px">Plant(min)<br>Planned : 30</span><span class="actual" style="top:18px">Actual : 33</span>
    </div>
    <div class="pop-row" style="top:150px;height:52px">
      <svg width="30" height="22" viewBox="0 0 22 16" style="top:15px;color:var(--popup-blue)"><use href="#i-truck"/></svg>
      <span class="desc" style="top:10px">Driving(min)<br>Planned : 60</span><span class="actual" style="top:18px">Actual : 83</span>
    </div>
    <div class="pop-row" style="top:202px;height:53px">
      <svg width="18" height="26" viewBox="0 0 14 20" style="top:13px;left:20px;color:var(--popup-blue)"><use href="#i-pin-solid"/></svg>
      <span class="desc" style="top:10px">Jobsite(min)<br>Planned : 30</span><span class="actual" style="top:18px">Actual : 33</span>
    </div>
    <div class="pop-row" style="top:255px;height:60px">
      <svg width="32" height="24" viewBox="0 0 32 24" style="top:18px"><g fill="var(--popup-blue)"><path d="M2 16V9h8l3-6h6l2 6h4l4 7z"/><circle cx="8" cy="19" r="3.5"/><circle cx="24" cy="19" r="3.5"/><path d="M26 9l5-5 1 1-5 5z"/></g></svg>
      <span class="desc" style="top:24px">Equipment(min)</span><span class="actual" style="top:24px">Actual : -</span>
    </div>
  </div>
</section>

</div>
</body>
</html>
```